Business Card Design For Office Furniture Clearance Company

Kestrel Office Clearance - our company name pretty much explains what we do, we clear offices for high end clients, mainly plc's and large international companies.

We require a nice looking business card that displays professionalism but without being too serious.

It would be nice to see just a little more than a conventional boring business card, make sure you add some flare.

Industry/Entity Type

Office Furniture

Contact Information for Business Card

CARD 1

Mark Holloway
Director
mark@kestrelofficeclearance.co.uk
m: 07700 153928

t: 01632 960418
www.kestrelofficeclearance.co.uk

Kestrel Office Clearance
Unit K4 B
2-8 Fenwick Lane
Ashcombe
Fernley Vale
ZZ9 4QT

free office clearances… simply the smartest move.

CARD 2

Peter Radford
Director
peter@kestrelofficeclearance.co.uk
m: 07700 382615

t: 01632 960418

Kestrel Office Clearance
Unit K4 B
2-8 Fenwick Lane
Ashcombe
Fernley Vale
ZZ9 4QT

Font styles to use
Sans Serif

Requirements
Must have
• A white background - as we have a blue logo.
Nice to have
• Nice use of the logo - play around with this and dissect it.

```html
<!DOCTYPE html>
<html lang="en">
<head>
<meta charset="utf-8">
<title>Kestrel Office Clearance – Business Card</title>
<link href="https://fonts.googleapis.com/css2?family=Open+Sans:wght@400;600;700&display=swap" rel="stylesheet">
<style>
  :root {
    --stage-top: #2a2a2a;
    --stage-bottom: #060606;
    --card-white: #ffffff;
    --brand-blue: #0a74b9;
    --brand-deep: #0a5f90;
    --brand-mid: #0b78b8;
    --brand-light: #6db6e6;
    --ink: #222222;
  }
  * { margin: 0; padding: 0; box-sizing: border-box; }
  html, body { width: 1200px; height: 900px; overflow: hidden; }
  body {
    position: relative;
    background: linear-gradient(180deg, var(--stage-top) 0%, #141414 55%, var(--stage-bottom) 100%);
    font-family: "Open Sans", sans-serif;
  }
  .card {
    position: absolute;
    top: 306px;
    width: 440px;
    height: 271px;
    border-radius: 10px;
  }
  .card-front { left: 149px; background: var(--card-white); }
  .card-back { left: 608px; background: var(--brand-deep); }

  .brand-mark { position: absolute; left: 36px; top: 44px; width: 158px; text-align: center; }
  .brand-mark .dot {
    width: 112px; height: 112px; margin: 0 auto;
    border-radius: 50%; background: var(--brand-mid);
  }
  .brand-mark .brand-name {
    margin-top: 10px; font-size: 13px; font-weight: 700;
    color: var(--brand-blue); line-height: 16px;
  }

  .details { position: absolute; left: 221px; top: 32px; color: var(--ink); }
  .person-name { font-size: 15px; font-weight: 600; color: var(--brand-blue); line-height: 20px; }
  .person-role { font-size: 11.5px; line-height: 14px; }
  .company-name { margin-top: 12px; font-size: 13.5px; font-weight: 700; color: var(--brand-blue); line-height: 18px; }
  .address { font-size: 11.5px; line-height: 16px; }
  .contacts { list-style: none; margin-top: 10px; font-size: 11.5px; line-height: 15.8px; }
  .contacts li { display: flex; align-items: center; gap: 8px; white-space: nowrap; }
  .contacts svg { width: 9px; height: 9px; fill: var(--brand-blue); flex: none; }

  .tagline {
    position: absolute; left: 0; right: 0; top: 219px;
    text-align: center; font-size: 13.5px; font-weight: 600; color: var(--brand-blue);
  }

  .back-mark { position: absolute; left: 0; right: 0; top: 40px; text-align: center; }
  .back-mark .dot {
    width: 150px; height: 150px; margin: 0 auto; border-radius: 50%;
    background: var(--brand-mid);
    box-shadow: inset 0 0 0 1px rgba(255,255,255,0.25), 0 0 0 1px rgba(0,0,0,0.2);
  }
  .back-mark .brand-name {
    margin-top: 16px; font-size: 14px; font-weight: 700; color: var(--brand-light);
  }
</style>
</head>
<body>
  <section class="card card-front">
    <div class="brand-mark">
      <div class="dot"></div>
      <p class="brand-name">Kestrel Office<br>Clearance</p>
    </div>
    <div class="details">
      <p class="person-name">Mark Holloway</p>
      <p class="person-role">Director</p>
      <p class="company-name">Kestrel Office Clearance</p>
      <p class="address">Unit K4 B,2-8 Fenwick Lane<br>Ashcombe,Fernley Vale,ZZ9 4QT</p>
      <ul class="contacts">
        <li><svg viewBox="0 0 10 10"><path d="M3 0h4a1 1 0 0 1 1 1v8a1 1 0 0 1-1 1H3a1 1 0 0 1-1-1V1a1 1 0 0 1 1-1zm0 1.5v6h4v-6z"/></svg>07700 153928</li>
        <li><svg viewBox="0 0 10 10"><path d="M2 0l2 2.2-1 1.3a6 6 0 0 0 3.5 3.5l1.3-1L10 8l-1.5 1.8C4 10 0 6 .2 1.5z"/></svg>01632 960418</li>
        <li><svg viewBox="0 0 10 10"><path d="M0 2h10v6H0zm1 .8v.4l4 2.6 4-2.6v-.4z"/></svg>mark@kestrelofficeclearance.co.uk</li>
        <li><svg viewBox="0 0 10 10"><circle cx="5" cy="5" r="5"/></svg>www.kestrelofficeclearance.co.uk</li>
      </ul>
    </div>
    <p class="tagline">free office clearances… simply the smartest move.</p>
  </section>

  <section class="card card-back">
    <div class="back-mark">
      <div class="dot"></div>
      <p class="brand-name">Kestrel Office Clearance</p>
    </div>
  </section>
</body>
</html>
```